Business Card Design - Amberfield Court

We are looking at a new design for our business cards that has a modern and professional look. We run a residential aged care facility focussing on the care of residents. The cards will be used for potential clients, consultants and business opportunities in this sector. Blue and white is our main colours and would to see these colours incorporated in the design.
Industry/Entity Type
Business
Contact Information for Business Card
Amberfield Court, Darren Walsh, dwalsh@amberfieldcourt.com.au, Finance Manager, 0472 639 208, BCom, 37 Marrabel Crescent, Brindle Vale, Qld 4093.
Look and feel
Each slider illustrates characteristics of the customer's brand and the style your logo design should communicate.

```html
<!DOCTYPE html>
<html lang="en">
<head>
<meta charset="utf-8">
<title>Amberfield Court – Business Card</title>
<link href="https://fonts.googleapis.com/css2?family=Arimo:wght@400;700&display=swap" rel="stylesheet">
<style>
  :root {
    --page-bg: #e8e5e0;
    --card-white: #ffffff;
    --card-white-shade: #eceeef;
    --brand-blue: #4b7892;
    --brand-blue-deep: #3a6379;
    --rule-grey: #b9b4ae;
    --text-light: #f3f6f8;
    --name-blue: #4b7892;
  }
  * { box-sizing: border-box; margin: 0; padding: 0; }
  html, body {
    width: 1200px;
    height: 950px;
    overflow: hidden;
    background: var(--page-bg);
    font-family: "Arimo", Arial, sans-serif;
  }
  .stage {
    width: 1200px;
    height: 950px;
    display: flex;
    flex-direction: column;
    align-items: center;
    justify-content: center;
    gap: 30px;
  }
  .card {
    position: relative;
    width: 760px;
    height: 434px;
    overflow: hidden;
    box-shadow: 0 6px 18px rgba(0,0,0,0.18);
  }

  /* Front */
  .card-front { background: var(--brand-blue); }
  .front-top {
    position: absolute;
    left: 0; top: 0;
    width: 100%;
    height: 245px;
    background: linear-gradient(180deg, var(--card-white) 0%, var(--card-white-shade) 100%);
    display: flex;
    align-items: center;
    justify-content: center;
  }
  .front-rule {
    position: absolute;
    left: 0; top: 245px;
    width: 100%;
    height: 4px;
    background: var(--rule-grey);
  }
  .front-band {
    position: absolute;
    left: 0; top: 249px;
    width: 100%;
    height: 185px;
    background: linear-gradient(180deg, var(--brand-blue) 0%, var(--brand-blue-deep) 100%);
  }
  .brand-mark {
    display: flex;
    align-items: center;
    gap: 14px;
    margin-left: 90px;
  }
  .brand-dot {
    width: 26px; height: 26px;
    border-radius: 50%;
    background: var(--brand-blue);
  }
  .brand-name {
    font-size: 34px;
    font-weight: 400;
    letter-spacing: 3px;
    color: var(--brand-blue);
    text-transform: uppercase;
  }
  .contact {
    position: absolute;
    top: 272px;
    left: 0;
    width: 100%;
    display: flex;
    color: var(--text-light);
  }
  .contact-person {
    width: 372px;
    text-align: right;
    padding-right: 20px;
    font-size: 18px;
    line-height: 24px;
  }
  .person-name { font-size: 22px; font-weight: 700; line-height: 28px; }
  .person-name .credential { font-size: 18px; }
  .contact-divider {
    width: 1px;
    height: 118px;
    background: var(--text-light);
    opacity: 0.8;
  }
  .contact-details {
    padding-left: 18px;
    font-size: 18px;
    line-height: 24px;
  }
  .detail-line { display: flex; align-items: center; gap: 10px; }
  .detail-gap { height: 6px; }
  .detail-icon { width: 16px; height: 16px; flex: none; }

  /* Back */
  .card-back {
    background: linear-gradient(135deg, var(--brand-blue) 0%, var(--brand-blue-deep) 100%);
    display: flex;
    flex-direction: column;
    align-items: center;
    justify-content: center;
    gap: 18px;
  }
  .back-name {
    font-size: 40px;
    font-weight: 400;
    letter-spacing: 4px;
    text-transform: uppercase;
    color: var(--card-white);
  }
  .back-web {
    font-size: 22px;
    letter-spacing: 1px;
    color: var(--card-white);
  }
</style>
</head>
<body>
<main class="stage">

  <section class="card card-front" aria-label="Business card front">
    <div class="front-top">
      <div class="brand-mark">
        <span class="brand-dot"></span>
        <span class="brand-name">Amberfield Court</span>
      </div>
    </div>
    <div class="front-rule"></div>
    <div class="front-band"></div>

    <div class="contact">
      <div class="contact-person">
        <p class="person-name">Darren Walsh <span class="credential">BCom</span></p>
        <p class="person-role">Finance Manager</p>
        <p class="person-email">dwalsh@amberfieldcourt.com.au</p>
      </div>
      <div class="contact-divider"></div>
      <div class="contact-details">
        <p>37 Marrabel Crescent</p>
        <p>Brindle Vale, Qld 4093.</p>
        <div class="detail-gap"></div>
        <p class="detail-line">
          <svg class="detail-icon" viewBox="0 0 16 16" aria-hidden="true">
            <circle cx="8" cy="8" r="8" fill="#f3f6f8"/>
            <path d="M5 4.2l1.6-.4 1 2.2-1 .8c.5 1.1 1.2 1.8 2.3 2.3l.8-1 2.2 1-.4 1.6c-3.3.3-6.8-3.2-6.5-6.5z" fill="#3a6379"/>
          </svg>
          0472 639 208
        </p>
        <p class="detail-line">
          <svg class="detail-icon" viewBox="0 0 16 16" aria-hidden="true">
            <circle cx="8" cy="8" r="8" fill="#f3f6f8"/>
            <circle cx="8" cy="8" r="4.5" fill="none" stroke="#3a6379" stroke-width="1.2"/>
            <path d="M3.5 8h9M8 3.5c-2 2.5-2 6.5 0 9M8 3.5c2 2.5 2 6.5 0 9" fill="none" stroke="#3a6379" stroke-width="1"/>
          </svg>
          www.amberfieldcourt.com.au
        </p>
      </div>
    </div>
  </section>

  <section class="card card-back" aria-label="Business card back">
    <p class="back-name">Amberfield Court</p>
    <p class="back-web">amberfieldcourt.com.au</p>
  </section>

</main>
</body>
</html>
```